Website Design for Employee Moral and Happiness Company

Looking for a clean website design that explains our features in a step by step manner so our visitors know exactly what our site does before logging in.

The site is called "Velrato". See logo design and video for a sample of style and an overview of what we do.

Target Market(s)

Business owners that are looking to retain employees.

Number of Pages Required

1 page

```html
<!DOCTYPE html>
<html lang="en">
<head>
<meta charset="utf-8">
<title>Velrato</title>
<link href="https://fonts.googleapis.com/css2?family=Oswald:wght@500;600&family=Lato:ital,wght@0,400;0,700;1,400&display=swap" rel="stylesheet">
<style>
:root{
  --orange:#e8501c;
  --ink:#1c1c1c;
  --text:#444;
  --muted:#666;
  --light:#f2f3f5;
  --rust:#a8401a;
  --footer:#121212;
  --white:#fff;
}
*{box-sizing:border-box;margin:0;padding:0}
html,body{width:1200px;height:3824px;overflow:hidden}
body{font-family:'Lato',sans-serif;color:var(--text);background:var(--white);position:relative}
.abs{position:absolute}
h2{font-family:'Oswald',sans-serif;font-weight:600;color:var(--ink);font-size:42px;letter-spacing:.5px}
.center{left:0;width:1200px;text-align:center}
.btn{position:absolute;display:flex;align-items:center;justify-content:center;background:var(--orange);color:var(--white);border-radius:26px;font-size:17px;font-weight:700;text-transform:uppercase}
.brand{font-family:'Lato',sans-serif;font-weight:700;color:var(--ink);font-size:56px;letter-spacing:1px;display:flex;align-items:center;gap:12px}
.brand i{display:block;width:16px;height:16px;border-radius:50%;background:var(--orange)}
.ring{width:34px;height:34px;border-radius:50%;border:2px solid var(--ink)}
/* header */
.header{top:0;left:0;width:1200px;height:103px;background:var(--white)}
.nav{position:absolute;top:62px;left:450px;display:flex;gap:0;font-size:16px;font-weight:700;color:var(--ink)}
.nav span{margin-right:47px}
.nav span.active{color:var(--orange)}
.phone{position:absolute;top:10px;left:680px;display:flex;align-items:center;gap:10px;font-size:19px;color:var(--ink)}
.phone b{width:36px;height:36px;border-radius:50%;background:var(--orange);display:flex;align-items:center;justify-content:center}
.social{position:absolute;top:10px;left:910px;display:flex;gap:10px}
.social::before{content:"";position:absolute;left:-18px;top:-2px;width:1px;height:40px;background:#ccc}
/* hero */
.hero{top:103px;left:0;width:1200px;height:681px;background:linear-gradient(90deg,#5a6468 0%,#8a8d8c 45%,#b9b2a8 70%,#4f5256 100%)}
.hero h1{position:absolute;left:111px;top:188px;font-family:'Oswald',sans-serif;font-weight:600;font-size:104px;color:var(--white);letter-spacing:1px}
.hero p{position:absolute;left:114px;top:320px;width:460px;font-size:17px;font-weight:700;color:var(--white);line-height:31px}
.arrow{position:absolute;width:22px;height:22px;border-left:2px solid var(--white);border-bottom:2px solid var(--white)}
.dots{position:absolute;top:636px;left:562px;display:flex;gap:10px}
.dots i{width:12px;height:12px;border-radius:50%;background:rgba(255,255,255,.5)}
.dots i.on{background:var(--white)}
/* about */
.about-art{left:114px;top:872px;width:446px;height:422px;border:4px solid var(--ink);border-radius:6px}
.about-fill{left:133px;top:888px;width:443px;height:422px;background:linear-gradient(135deg,#e6ddd2,#d7cbbd 60%,#c9d6d0);border-radius:4px}
.play{left:515px;top:1256px;width:61px;height:54px;background:var(--orange);display:flex;align-items:center;justify-content:center}
.about-text{left:645px;top:882px;width:440px}
.about-text p{font-size:15px;line-height:28.5px;color:var(--text);margin-top:14px}
/* features */
.features{top:1396px;left:0;width:1200px;height:541px;background:var(--light)}
.feature{position:absolute;top:160px;width:304px;height:304px;border-radius:50%;background:var(--ink);color:var(--white);text-align:center;padding-top:50px}
.feature.hot{background:var(--orange)}
.feature h3{font-size:18px;font-weight:700;margin-top:18px;letter-spacing:.3px}
.feature p{font-size:13.5px;line-height:21.5px;margin:8px auto 0;width:220px}
.feature .down{display:block;margin:12px auto 0}
/* testimonials */
.testi{top:1937px;left:0;width:1200px;height:490px;background:linear-gradient(120deg,#2e2b2a,#3d3836 50%,#262321)}
.testi h2{color:var(--white);position:absolute;top:84px}
.quote{position:absolute;top:170px;left:200px;width:820px;text-align:center;font-style:italic;font-size:19.5px;line-height:37px;color:var(--white)}
.qmark{position:absolute;font-family:'Oswald',sans-serif;font-size:72px;color:var(--orange);line-height:1}
.avatar{position:absolute;left:497px;top:324px;width:70px;height:70px;border-radius:50%;background:linear-gradient(#c9cfd4,#8e969c)}
.who{position:absolute;left:585px;top:337px;color:var(--white)}
.who b{display:block;font-size:21px;font-weight:700}
.who span{font-size:15px}
/* blog */
.card{position:absolute;top:2560px;width:312px;height:385px;background:var(--white);box-shadow:0 2px 12px rgba(0,0,0,.1)}
.card .pic{height:195px}
.card h4{margin:18px 14px 0;font-size:17.5px;font-weight:700;color:var(--ink);line-height:26px}
.card p{margin:10px 14px 0;font-size:13px;line-height:23px;color:var(--muted)}
.card a{display:block;margin:14px 14px 0;font-size:13px;font-weight:700;color:var(--orange);text-decoration:underline}
/* contact */
.contact{top:3027px;left:0;width:1200px;height:460px;background:linear-gradient(180deg,#a8401a,#9b3a17)}
.contact h2{color:var(--white);position:absolute;top:70px}
.field{position:absolute;border:1.5px solid rgba(255,255,255,.7);color:var(--white);font-size:15px;padding:14px 17px}
.submit{position:absolute;left:506px;top:328px;width:188px;height:49px;border-radius:26px;background:#f1faf7;color:var(--orange);display:flex;align-items:center;justify-content:center;font-size:18px;font-weight:700}
/* footer */
.footer{top:3487px;left:0;width:1200px;height:337px;background:var(--footer);color:var(--white)}
.footer h5{font-size:18px;font-weight:700;text-transform:uppercase}
.links{font-size:14px;line-height:26.5px;margin-top:12px}
.fcontact{font-size:14px}
.fcontact div{display:flex;gap:8px;align-items:flex-start;margin-top:16px;line-height:20px}
.fring{width:38px;height:38px;border-radius:50%;border:2px solid var(--white)}
.email{position:absolute;left:766px;top:114px;width:311px;height:49px;border:1.5px solid var(--white);border-radius:26px;font-size:14px;padding:15px 20px}
.sub{position:absolute;left:766px;top:178px;width:311px;height:49px;border-radius:26px;background:var(--orange);display:flex;align-items:center;justify-content:center;font-size:16px;font-weight:700}
.rule{position:absolute;left:111px;top:281px;width:978px;height:1px;background:#333}
.copy{position:absolute;top:298px;left:0;width:1200px;text-align:center;font-size:14px}
</style>
</head>
<body>

<header class="abs header">
  <div class="abs brand" style="left:111px;top:14px">velrato<i></i></div>
  <div class="phone"><b><svg width="18" height="18" viewBox="0 0 24 24"><path d="M6.6 10.8a15 15 0 0 0 6.6 6.6l2.2-2.2a1 1 0 0 1 1-.25 11.4 11.4 0 0 0 3.6.57 1 1 0 0 1 1 1V20a1 1 0 0 1-1 1A17 17 0 0 1 3 4a1 1 0 0 1 1-1h3.5a1 1 0 0 1 1 1c0 1.25.2 2.45.57 3.57a1 1 0 0 1-.25 1z" fill="#fff"/></svg></b>+1 555.014.2290</div>
  <div class="social"><div class="ring"></div><div class="ring"></div><div class="ring"></div><div class="ring"></div></div>
  <nav class="nav"><span class="active">Home</span><span>About Us</span><span>Features</span><span>Latest News</span><span>Testimonial</span><span style="margin-right:0">Contact</span></nav>
</header>

<section class="abs hero">
  <div class="abs" role="img" aria-label="Smiling professional woman working on a laptop in a bright office" style="inset:0"></div>
  <h1>VELRATO</h1>
  <p>Sed ut perspiciatis unde o sit voluptatem accusantium doloremque laudantium, totam rem aperiam</p>
  <div class="btn" style="left:111px;top:406px;width:179px;height:49px">Get Started</div>
  <div class="arrow" style="left:88px;top:340px;transform:rotate(45deg)"></div>
  <div class="arrow" style="left:1108px;top:340px;transform:rotate(-135deg)"></div>
  <div class="dots"><i></i><i class="on"></i><i></i><i></i></div>
</section>

<section>
  <div class="abs about-art"></div>
  <div class="abs about-fill" role="img" aria-label="Illustration of a cheerful man holding up a profile card"></div>
  <div class="abs play"><svg width="20" height="22" viewBox="0 0 20 22"><path d="M2 1l17 10L2 21z" fill="#fff"/></svg></div>
  <div class="abs about-text">
    <h2>ABOUT US</h2>
    <p>Lorem ipsum dolor sit amet, consectetur adipiscing elit, sed do eiusmod tempor incididunt ut labore et dolore magna aliqua. Ut enim ad minim veniam, quis nostrud exercitation ullamco laboris nisi ut aliquip ex ea commodo consequat. Duis aute irure dolor in reprehenderit in voluptate velit esse</p>
    <p>Lorem ipsum dolor sit amet, consectetur adipiscing elit, sed do eiusmod tempor incididunt ut labore et dolore magna aliqua. Ut enim ad minim veniam, quis nostrud exercitation ullamco laboris nisi ut aliquip ex ea commodo consequat.</p>
  </div>
  <div class="btn" style="left:645px;top:1236px;width:179px;height:49px">Learn More</div>
</section>

<section class="abs features">
  <h2 class="abs center" style="top:66px">OUR FEATURES</h2>
  <div class="feature" style="left:114px">
    <svg width="70" height="70" viewBox="0 0 70 70" fill="none" stroke="#fff" stroke-width="2"><rect x="12" y="8" width="34" height="46" rx="2"/><path d="M18 20h22M18 28h22M18 36h14"/><circle cx="46" cy="46" r="12"/><path d="M55 55l8 8"/></svg>
    <h3>FINIBUS BONOR</h3>
    <p>Sed ut perspiciatis unde omnis iste natus ersit voluptatem accusantium doloremque laudantium,</p>
    <svg class="down" width="30" height="30" viewBox="0 0 30 30" fill="none" stroke="#fff" stroke-width="1.6"><circle cx="15" cy="15" r="13"/><path d="M9 13l6 6 6-6"/></svg>
  </div>
  <div class="feature hot" style="left:448px">
    <svg width="70" height="70" viewBox="0 0 70 70" fill="none" stroke="#fff" stroke-width="2"><circle cx="35" cy="20" r="10"/><circle cx="35" cy="20" r="4"/><circle cx="25" cy="44" r="5"/><circle cx="45" cy="44" r="5"/><path d="M17 64v-8a8 8 0 0 1 16 0v8M37 64v-8a8 8 0 0 1 16 0v8M52 14l10-8M8 22l8-6"/></svg>
    <h3>FINIBUS BONOR</h3>
    <p>Sed ut perspiciatis unde omnis iste natus ersit voluptatem accusantium doloremque laudantium,</p>
    <svg class="down" width="30" height="30" viewBox="0 0 30 30" fill="none" stroke="#fff" stroke-width="1.6"><circle cx="15" cy="15" r="13"/><path d="M9 13l6 6 6-6"/></svg>
  </div>
  <div class="feature" style="left:782px">
    <svg width="70" height="70" viewBox="0 0 70 70" fill="none" stroke="#fff" stroke-width="2"><rect x="10" y="8" width="50" height="32" rx="2"/><path d="M16 32l10-10 8 6 12-12 8 6"/><circle cx="20" cy="50" r="5"/><circle cx="35" cy="50" r="5"/><circle cx="50" cy="50" r="5"/><path d="M12 64a8 8 0 0 1 16 0M27 64a8 8 0 0 1 16 0M42 64a8 8 0 0 1 16 0"/></svg>
    <h3>FINIBUS BONOR</h3>
    <p>Sed ut perspiciatis unde omnis iste natus ersit voluptatem accusantium doloremque laudantium,</p>
    <svg class="down" width="30" height="30" viewBox="0 0 30 30" fill="none" stroke="#fff" stroke-width="1.6"><circle cx="15" cy="15" r="13"/><path d="M9 13l6 6 6-6"/></svg>
  </div>
</section>

<section class="abs testi" role="img" aria-label="Dimmed photo of colleagues laughing together at a desk">
  <h2 class="center">TESTIMONIALS</h2>
  <div class="qmark" style="left:162px;top:160px">&ldquo;</div>
  <p class="quote">Sed ut perspiciatis unde omnis iste natus error sit voluptatem accusantium doloremque laudantium, totam rem aperiam, eaque ipsa quae ab illo inventore veritatis et quasi architecto beatae vitae dicta sunt explicabo. Nemo enim ipsam voluptatem quia voluptas</p>
  <div class="qmark" style="left:863px;top:240px">&rdquo;</div>
  <div class="arrow" style="left:116px;top:208px;width:30px;height:30px;transform:rotate(45deg)"></div>
  <div class="arrow" style="left:1060px;top:208px;width:30px;height:30px;transform:rotate(-135deg)"></div>
  <div class="avatar" role="img" aria-label="Portrait of the reviewer"></div>
  <div class="who"><b>- Lena Hartwick</b><span>General Manager</span></div>
</section>

<section>
  <h2 class="abs center" style="top:2482px">LATEST BLOG</h2>
  <article class="card" style="left:111px">
    <div class="pic" role="img" aria-label="Team gathered around a laptop in an office" style="background:linear-gradient(135deg,#d9dde0,#8c949a)"></div>
    <h4>The standard Lorem Ipsum passage, used since</h4>
    <p>Sed ut peatus error sit voluptatem accusantium doremque laudantium, totamm aperiam, eaque ipsa quae ab illo inventore</p>
    <a>READ MORE...</a>
  </article>
  <article class="card" style="left:444px">
    <div class="pic" role="img" aria-label="Business handshake over a desk with laptops" style="background:linear-gradient(135deg,#6b6e70,#3a3c3e)"></div>
    <h4>The standard Lorem Ipsum passage, used since</h4>
    <p>Sed ut peatus error sit voluptatem accusantium doremque laudantium, totamm aperiam, eaque ipsa quae ab illo inventore</p>
    <a>READ MORE...</a>
  </article>
  <article class="card" style="left:777px">
    <div class="pic" role="img" aria-label="Colleagues shaking hands in a meeting room" style="background:linear-gradient(135deg,#e4e7ea,#9aa1a6)"></div>
    <h4>The standard Lorem Ipsum passage, used since</h4>
    <p>Sed ut peatus error sit voluptatem accusantium doremque laudantium, totamm aperiam, eaque ipsa quae ab illo inventore</p>
    <a>READ MORE...</a>
  </article>
</section>

<section class="abs contact">
  <h2 class="center">CONTACT US</h2>
  <div class="field" style="left:197px;top:138px;width:332px;height:49px">First Name</div>
  <div class="field" style="left:197px;top:194px;width:332px;height:49px">Email Address</div>
  <div class="field" style="left:197px;top:250px;width:332px;height:50px">Phone number</div>
  <div class="field" style="left:539px;top:138px;width:465px;height:162px">Message</div>
  <div class="submit">SUBMIT</div>
</section>

<footer class="abs footer">
  <div class="abs brand" style="left:111px;top:74px;font-size:46px;color:var(--white)">velrato</div>
  <div class="abs" style="left:113px;top:158px;display:flex;gap:10px"><div class="fring"></div><div class="fring"></div><div class="fring"></div><div class="fring"></div></div>
  <div class="abs" style="left:368px;top:76px">
    <h5>Explore</h5>
    <div class="links">Home<br>About Us<br>Features<br>Latest News<br>Testimonial<br>Contact</div>
  </div>
  <div class="abs fcontact" style="left:524px;top:76px">
    <h5>Contact Us</h5>
    <div><svg width="14" height="18" viewBox="0 0 14 18"><path d="M7 1a6 6 0 0 0-6 6c0 4.5 6 10 6 10s6-5.5 6-10a6 6 0 0 0-6-6z" fill="none" stroke="#fff" stroke-width="1.6"/><circle cx="7" cy="7" r="2" fill="#fff"/></svg><span>48 Harbor Lane,<br>Brookfield 20914, US</span></div>
    <div><svg width="16" height="16" viewBox="0 0 24 24"><path d="M6.6 10.8a15 15 0 0 0 6.6 6.6l2.2-2.2a1 1 0 0 1 1-.25 11.4 11.4 0 0 0 3.6.57 1 1 0 0 1 1 1V20a1 1 0 0 1-1 1A17 17 0 0 1 3 4a1 1 0 0 1 1-1h3.5a1 1 0 0 1 1 1c0 1.25.2 2.45.57 3.57a1 1 0 0 1-.25 1z" fill="#fff"/></svg><span>+1 555 014 2290</span></div>
    <div><svg width="16" height="14" viewBox="0 0 16 14"><rect x="1" y="2" width="14" height="10" fill="none" stroke="#fff" stroke-width="1.5"/><path d="M1 2l7 6 7-6" fill="none" stroke="#fff" stroke-width="1.5"/></svg><span>hello@velrato.com</span></div>
  </div>
  <h5 class="abs" style="left:765px;top:76px">Sign up for newsletter</h5>
  <div class="email">Email..</div>
  <div class="sub">SUBSCRIBE</div>
  <div class="rule"></div>
  <div class="copy">Copyright © 2022 Velrato. All rights reserved.</div>
</footer>

</body>
</html>
```